Business Cards for new orthopaedic surgery practice

My husband and I are starting our own orthopaedic surgery practice. We are looking for a business card that is uniform, but one will have my name/title and the other will have his. You can just create one design with my name on it for now. But when I choose your design as the winning design I will ask that you add another copy with his name/title.

We are looking for classy, simple, elite all in one. We like dark blues/a little gold/yellow. Something that goes with our logo. We want our logo incorporated. Here is all the info you need:
Business name: RV Bone & Vitality Center
Location: 38517 North Willowmere Ave
Maple Hollow, FL 34920
Phone: 954-218-4063
Fax: 954-582-7341
Email: info@myrvbonecare.example

Names: Lydia Vance, M.D.
Board Certified Hand and Upper Extremity Surgeon

Ebo Dansu, M.D.
Board Certified Hip & Knee Replacement/General Orthopaedic Surgeon

Can decide what you want to put on the back. Maybe a slogan:
Rooted in Care. Focused on You

I am just going to upload our logo. The only thing is if we select you as the winning design, the location, and phone numbers may change. We will need your help to update that once fully solidified.

Industry/Entity Type

Medical

Contact Information for Business Card

Colors
0054AA
0677BA
7BADD7
CADEEF
E8F1F8
0094D4
00A9DD
6FCCEA
C7EBF8
E9F6FB

Requirements
Must have
• class, appeal,
Should not have
• We want to air on the side of masculine if we are looking at masculine vs. feminine feel. But we still want it classy, sophisticated, and something we will love

```html
<!DOCTYPE html>
<html lang="en">
<head>
<meta charset="utf-8">
<title>RV Bone &amp; Vitality Center – Business Cards</title>
<link href="https://fonts.googleapis.com/css2?family=Gilda+Display&family=Poppins:wght@300;400;700&display=swap" rel="stylesheet">
<style>
  :root {
    --backdrop: #c4c4c4;
    --navy: #121d3d;
    --navy-deep: #0e1733;
    --navy-soft: #17244a;
    --gold: #c9a45a;
    --white: #ffffff;
    --ink-light: #f2f2f2;
  }
  * { margin: 0; padding: 0; box-sizing: border-box; }
  html, body { width: 800px; height: 1200px; overflow: hidden; }
  body {
    background: var(--backdrop);
    font-family: "Poppins", sans-serif;
    position: relative;
  }
  .card {
    position: absolute;
    left: 80px;
    width: 640px;
    height: 366px;
    box-shadow: 4px 6px 10px rgba(0,0,0,0.25);
    overflow: hidden;
  }
  .card-front {
    top: 204px;
    background: linear-gradient(160deg, var(--navy-soft) 0%, var(--navy) 45%, var(--navy-deep) 100%);
  }
  .card-back {
    top: 630px;
    background: var(--white);
  }
  .divider {
    position: absolute;
    left: 296px;
    top: 103px;
    width: 1.5px;
    height: 160px;
    background: var(--gold);
  }
  .doctor-name {
    position: absolute;
    left: 48px;
    top: 102px;
    font-family: "Gilda Display", serif;
    font-size: 32px;
    font-weight: 400;
    line-height: 41px;
    color: var(--gold);
    letter-spacing: 0;
    white-space: nowrap;
  }
  .doctor-title {
    position: absolute;
    left: 49px;
    top: 204px;
    padding-left: 10px;
    border-left: 2px solid var(--gold);
    font-size: 13.5px;
    line-height: 19px;
    font-weight: 400;
    color: var(--ink-light);
    letter-spacing: 0.8px;
    white-space: nowrap;
  }
  .contact-list {
    position: absolute;
    left: 356px;
    top: 112px;
    list-style: none;
    color: var(--ink-light);
    font-size: 15px;
    font-weight: 400;
    letter-spacing: 0.5px;
  }
  .contact-list li {
    display: flex;
    align-items: flex-start;
    margin-bottom: 18px;
    line-height: 20px;
    white-space: nowrap;
  }
  .contact-list svg {
    width: 16px;
    height: 16px;
    margin-top: 2px;
    margin-right: 8px;
    flex-shrink: 0;
    fill: var(--gold);
  }
  .brand-mark {
    position: absolute;
    left: 71px;
    top: 102px;
    width: 160px;
    height: 160px;
    border: 2px solid var(--gold);
    border-radius: 50%;
    display: flex;
    align-items: center;
    justify-content: center;
    text-align: center;
  }
  .brand-name {
    font-family: "Poppins", sans-serif;
    font-size: 14px;
    font-weight: 700;
    line-height: 20px;
    color: var(--navy);
    letter-spacing: 1px;
    text-transform: uppercase;
  }
  .slogan {
    position: absolute;
    left: 371px;
    top: 126px;
    font-size: 26px;
    line-height: 28px;
    letter-spacing: 3px;
    text-transform: uppercase;
    white-space: nowrap;
  }
  .slogan span { display: block; }
  .slogan .navy { color: var(--navy); font-weight: 400; }
  .slogan .gold { color: var(--gold); font-weight: 400; }
  .slogan .strong { font-weight: 700; }
</style>
</head>
<body>

  <section class="card card-front" aria-label="Business card front">
    <h1 class="doctor-name">LYDIA<br>VANCE, M.D.</h1>
    <p class="doctor-title">BOARD CERTIFIED<br>HAND &amp; UPPER<br>EXTREMITY SURGEON</p>
    <div class="divider"></div>
    <ul class="contact-list">
      <li>
        <svg viewBox="0 0 24 24" aria-hidden="true"><path d="M12 2a7 7 0 0 0-7 7c0 5 7 13 7 13s7-8 7-13a7 7 0 0 0-7-7zm0 9.5A2.5 2.5 0 1 1 12 6.5a2.5 2.5 0 0 1 0 5z"/></svg>
        <span>38517 North Willowmere Ave<br>Maple Hollow, FL 34920</span>
      </li>
      <li>
        <svg viewBox="0 0 24 24" aria-hidden="true"><path d="M6.6 10.8a15.1 15.1 0 0 0 6.6 6.6l2.2-2.2a1 1 0 0 1 1-.25 11.4 11.4 0 0 0 3.6.57 1 1 0 0 1 1 1V20a1 1 0 0 1-1 1A17 17 0 0 1 3 4a1 1 0 0 1 1-1h3.5a1 1 0 0 1 1 1c0 1.25.2 2.45.57 3.57a1 1 0 0 1-.25 1z"/></svg>
        <span>954-218-4063</span>
      </li>
      <li>
        <svg viewBox="0 0 24 24" aria-hidden="true"><path d="M7 3h10v4H7zM4 8h16a2 2 0 0 1 2 2v7h-4v4H6v-4H2v-7a2 2 0 0 1 2-2zm4 8v3h8v-3z"/></svg>
        <span>954-582-7341</span>
      </li>
      <li>
        <svg viewBox="0 0 24 24" aria-hidden="true"><path d="M2 5h20v14H2zm2 2v.4l8 5.3 8-5.3V7zm0 2.8V17h16V9.8l-8 5.3z"/></svg>
        <span>info@myrvbonecare.example</span>
      </li>
    </ul>
  </section>

  <section class="card card-back" aria-label="Business card back">
    <div class="brand-mark">
      <span class="brand-name">RV Bone &amp;<br>Vitality<br>Center</span>
    </div>
    <div class="divider"></div>
    <p class="slogan">
      <span class="navy">Grounded in</span>
      <span class="navy strong">Trust</span>
      <span class="gold">Devoted to</span>
      <span class="gold strong">You</span>
    </p>
  </section>

</body>
</html>
```